Property development business card design

New build residential property developers. I want a professional look but customer friendly so not too corporate. I'm not sure what logo will look best so open to designs with either. Thank you

Also i don't want both names on one card its 2 names for 2 different cards but with the same design.

Industry/Entity Type

Residential

Contact Information for Business Card

KTR Developments Ltd,
58 Fennel Lane,
Ipswich,
Suffolk,
IP7 4WD

Property Research Manager
Morven Tadlock

Managing Director
Dilan Perriwick

```html
<!DOCTYPE html>
<html lang="en">
<head>
<meta charset="utf-8">
<title>KTR Developments – Business Card</title>
<link rel="stylesheet" href="https://fonts.googleapis.com/css2?family=Open+Sans:wght@400;600;700&display=swap">
<style>
  :root {
    --page: #ecebe8;
    --card-white: #ffffff;
    --card-dark: #3a3b3d;
    --card-dark-deep: #2a2b2d;
    --brand-blue: #1f78c8;
    --brand-green: #8cc63f;
    --text-grey: #6d6e71;
    --text-dark: #333436;
    --text-light: #d9dadc;
    --faint: #e8eef6;
  }
  * { box-sizing: border-box; margin: 0; padding: 0; }
  html, body {
    width: 1200px; height: 784px; overflow: hidden;
    background: var(--page);
    font-family: "Open Sans", Arial, sans-serif;
  }
  .canvas { position: relative; width: 1200px; height: 784px; }

  .card {
    position: absolute; width: 600px; height: 350px;
    border-radius: 4px; overflow: hidden;
    box-shadow: 0 6px 18px rgba(0,0,0,0.18);
  }

  /* Back side */
  .card--back {
    left: 60px; top: 50px;
    background: radial-gradient(ellipse at 50% 40%, var(--card-dark) 0%, var(--card-dark-deep) 100%);
    display: flex; flex-direction: column; align-items: center; justify-content: center;
    gap: 18px;
  }
  .back-mark {
    width: 96px; height: 96px; border-radius: 50%;
    background: var(--brand-blue);
  }
  .back-name {
    color: var(--text-light); font-weight: 600;
    font-size: 30px; letter-spacing: 2px; text-transform: uppercase;
  }

  /* Front side */
  .card--front {
    left: 540px; top: 384px;
    background: var(--card-white);
  }
  .front-watermark {
    position: absolute; right: -40px; top: 70px;
    width: 200px; height: 200px; border-radius: 50%;
    background: var(--faint);
  }
  .holder {
    position: absolute; right: 26px; top: 20px; text-align: right;
  }
  .holder-name { color: var(--brand-blue); font-weight: 700; font-size: 19px; line-height: 1.2; }
  .holder-title { color: var(--text-dark); font-weight: 600; font-size: 12px; margin-top: 2px; }

  .brand {
    position: absolute; left: 34px; top: 76px;
    display: flex; align-items: center; gap: 14px;
  }
  .brand-mark { width: 64px; height: 64px; border-radius: 50%; background: var(--brand-blue); flex: none; }
  .brand-name {
    color: var(--text-grey); font-weight: 600; font-size: 24px;
    letter-spacing: 1.5px; text-transform: uppercase;
  }

  .contact {
    position: absolute; left: 34px; top: 172px;
    list-style: none; color: var(--text-dark); font-size: 15px; line-height: 24px;
  }
  .contact li { display: flex; align-items: flex-start; gap: 9px; }
  .contact svg { width: 14px; height: 14px; margin-top: 5px; flex: none; fill: var(--brand-blue); }
  .contact .indent { padding-left: 23px; }

  .front-rule {
    position: absolute; left: 0; right: 0; bottom: 30px; height: 4px;
    background: var(--brand-blue);
  }
  .front-band {
    position: absolute; left: 0; right: 0; bottom: 0; height: 30px;
    background: linear-gradient(var(--card-dark), var(--card-dark-deep));
  }
</style>
</head>
<body>
<main class="canvas">

  <section class="card card--back" aria-label="Business card back">
    <div class="back-mark"></div>
    <div class="back-name">KTR Developments</div>
  </section>

  <section class="card card--front" aria-label="Business card front">
    <div class="front-watermark"></div>

    <div class="holder">
      <div class="holder-name">Morven Tadlock</div>
      <div class="holder-title">Property Research Manager</div>
    </div>

    <div class="brand">
      <div class="brand-mark"></div>
      <div class="brand-name">KTR Developments</div>
    </div>

    <ul class="contact">
      <li>
        <svg viewBox="0 0 24 24" aria-hidden="true"><path d="M6.6 10.8a15.1 15.1 0 0 0 6.6 6.6l2.2-2.2a1 1 0 0 1 1-.25 11.4 11.4 0 0 0 3.6.57 1 1 0 0 1 1 1V20a1 1 0 0 1-1 1A17 17 0 0 1 3 4a1 1 0 0 1 1-1h3.5a1 1 0 0 1 1 1c0 1.25.2 2.45.57 3.57a1 1 0 0 1-.25 1z"/></svg>
        154 672 309
      </li>
      <li>
        <svg viewBox="0 0 24 24" aria-hidden="true"><path d="M12 2a10 10 0 1 0 0 20 10 10 0 0 0 0-20zm6.9 6h-2.9a15.6 15.6 0 0 0-1.4-3.6A8 8 0 0 1 18.9 8zM12 4a14 14 0 0 1 1.9 4h-3.8A14 14 0 0 1 12 4zM4.3 14a8 8 0 0 1 0-4h3.4a16.5 16.5 0 0 0 0 4zm.8 2h2.9a15.6 15.6 0 0 0 1.4 3.6A8 8 0 0 1 5.1 16zM8 8H5.1a8 8 0 0 1 4.3-3.6A15.6 15.6 0 0 0 8 8zm4 12a14 14 0 0 1-1.9-4h3.8A14 14 0 0 1 12 20zm2.3-6H9.7a14.7 14.7 0 0 1 0-4h4.6a14.7 14.7 0 0 1 0 4zm.3 5.6a15.6 15.6 0 0 0 1.4-3.6h2.9a8 8 0 0 1-4.3 3.6zm1.7-5.6a16.5 16.5 0 0 0 0-4h3.4a8 8 0 0 1 0 4z"/></svg>
        www.ktrdevelopments.co.uk
      </li>
      <li>
        <svg viewBox="0 0 24 24" aria-hidden="true"><path d="M3 5h18a1 1 0 0 1 1 1v12a1 1 0 0 1-1 1H3a1 1 0 0 1-1-1V6a1 1 0 0 1 1-1zm9 7.5L20 7H4z"/></svg>
        hello@ktrdevelopments.co.uk
      </li>
      <li>
        <svg viewBox="0 0 24 24" aria-hidden="true"><path d="M12 3l10 9h-3v9h-5v-6h-4v6H5v-9H2z"/></svg>
        58 Fennel Lane, Ipswich,
      </li>
      <li class="indent">Suffolk, IP7 4WD</li>
    </ul>

    <div class="front-rule"></div>
    <div class="front-band"></div>
  </section>

</main>
</body>
</html>
```